Jolly Hounds Dog Behaviour, Training and Natural Healthcare Business Card Design

I am an experienced and qualified dog behavioural trainer and natural animal healthcare consultant offering a range of services to help pet dog owners with the "whole dog".
COLOURS: A soft light blue in the background - can be fading out or split, red should also feature
LOGO: Dog, healing hands, silhouette, shadow
SERVICES: Behaviour Consults, Training, Complex Skills Coaching Walking Coaching, Diet & Nutrition, Environmental Enrichment, Lifestyle and Lifestage Adaptations, Massage, Natural Health Options
BY LINE: Happy Dogs, Happy Owners
VALUES: Promoting communication and connection between dogs and their owners.
FOCUS: Nutritional guidance and environmental adaptation are often needed to complete the package and increase the success rate of training and behaviour modification.

Target Market(s)

Everyone who has a dog who they wish to improve their relationship with

Industry/Entity Type

Communication

Contact Information for Business Card

Jolly Hounds, Rebecca Thornbury, 0427 861350, jollyhounds7@fernpost.example, www.jollyhounds7.example, Qualified Dog Behavioural Trainer and Natural Animal Healthcare Consultant

Font styles to use
Sans Serif
Script

Colors
85cae6
ec2027

Requirements
Must have
• A clear indication that it is a dog services business. A raised feature
Should not have
• Pawprints, cartoons

```html
<!DOCTYPE html>
<html lang="en">
<head>
<meta charset="UTF-8">
<title>Jolly Hounds Business Card</title>
<link rel="stylesheet" href="https://fonts.googleapis.com/css2?family=Cabin:wght@400;500;600&family=Encode+Sans+Condensed:wght@300&display=swap">
<style>
  :root {
    --page-bg: #2b2b2c;
    --band-grey: #7e7c7b;
    --brand-blue: #85cae6;
    --brand-red: #ec2027;
    --divider-dark: #2a2522;
    --photo-light: #e9bf7f;
    --photo-mid: #cf9550;
    --photo-deep: #98602a;
    --text-light: #ffffff;
    --text-soft: #f1eeea;
  }
  * { margin: 0; padding: 0; box-sizing: border-box; }
  html, body { width: 1200px; height: 900px; overflow: hidden; }
  body {
    background: var(--page-bg);
    display: flex;
    align-items: center;
    justify-content: center;
    font-family: "Cabin", sans-serif;
  }
  .business-card {
    position: relative;
    width: 1000px;
    height: 572px;
    background: var(--band-grey);
    overflow: hidden;
    box-shadow: 0 18px 40px rgba(0,0,0,0.45);
  }
  .puppy-photo {
    position: absolute;
    left: 0; top: 0;
    width: 100%;
    height: 300px;
    background:
      radial-gradient(ellipse 30% 45% at 80% 72%, var(--photo-light) 0%, transparent 100%),
      radial-gradient(ellipse 35% 50% at 32% 58%, var(--photo-light) 0%, transparent 100%),
      radial-gradient(ellipse 22% 35% at 62% 30%, var(--photo-mid) 0%, transparent 100%),
      linear-gradient(100deg, var(--brand-blue) 0%, var(--photo-mid) 12%, var(--photo-light) 45%, var(--photo-mid) 78%, var(--photo-deep) 94%, var(--brand-blue) 100%);
  }
  .photo-divider {
    position: absolute;
    left: 0; top: 300px;
    width: 100%;
    height: 8px;
    background: var(--divider-dark);
    border-top: 3px solid var(--brand-red);
    border-bottom: 2px solid var(--brand-blue);
  }
  .brand-block {
    position: absolute;
    top: 84px;
    left: 0;
    width: 100%;
    text-align: center;
    color: var(--text-light);
    text-shadow: 0 1px 4px rgba(0,0,0,0.45);
  }
  .brand-name {
    font-size: 50px;
    font-weight: 600;
    letter-spacing: 0.5px;
    margin-left: 130px;
  }
  .brand-title {
    font-size: 27px;
    font-weight: 400;
    line-height: 1.25;
    letter-spacing: 0.3px;
  }
  .brand-title .line-one { display: block; margin-left: 40px; }
  .owner-name {
    position: absolute;
    left: 100px;
    top: 358px;
    font-family: "Encode Sans Condensed", sans-serif;
    font-weight: 300;
    font-size: 42px;
    color: var(--text-soft);
  }
  .contact-list {
    position: absolute;
    left: 520px;
    top: 410px;
    list-style: none;
    color: var(--text-soft);
    font-size: 27px;
    line-height: 38px;
    letter-spacing: 0.4px;
  }
  .contact-list li { display: flex; align-items: center; }
  .contact-icon { width: 20px; height: 20px; margin-right: 18px; flex: none; }
  .card-footer-rule {
    position: absolute;
    left: 0; bottom: 0;
    width: 100%;
    height: 6px;
    background: linear-gradient(90deg, var(--brand-blue) 0%, var(--brand-blue) 70%, var(--brand-red) 70%, var(--brand-red) 100%);
  }
</style>
</head>
<body>
  <article class="business-card">
    <div class="puppy-photo" role="img" aria-label="Photograph of a group of golden retriever puppies against a light blue backdrop"></div>
    <div class="photo-divider"></div>

    <header class="brand-block">
      <h1 class="brand-name">Jolly Hounds</h1>
      <p class="brand-title">
        <span class="line-one">Qualified Dog Behavioural</span>
        <span>Trainer and Natural Animal Healthcare Consultant</span>
      </p>
    </header>

    <p class="owner-name">Rebecca Thornbury</p>

    <ul class="contact-list">
      <li>
        <svg class="contact-icon" viewBox="0 0 20 20" aria-hidden="true">
          <path d="M6 2 L9 2 L9 6 L7 7 Q8 11 11 13 L12 11 L16 11 L16 15 Q14 18 11 17 Q4 14 3 6 Q3 3 6 2 Z" fill="#85cae6"/>
        </svg>
        <span>0427 861350</span>
      </li>
      <li>
        <svg class="contact-icon" viewBox="0 0 20 20" aria-hidden="true">
          <rect x="1" y="4" width="18" height="12" fill="#85cae6"/>
          <path d="M1 4 L10 11 L19 4" fill="none" stroke="#7e7c7b" stroke-width="1.5"/>
        </svg>
        <span>jollyhounds7@fernpost.example</span>
      </li>
      <li>
        <svg class="contact-icon" viewBox="0 0 20 20" aria-hidden="true">
          <circle cx="10" cy="10" r="8" fill="none" stroke="#85cae6" stroke-width="1.5"/>
          <ellipse cx="10" cy="10" rx="3.5" ry="8" fill="none" stroke="#85cae6" stroke-width="1.2"/>
          <line x1="2" y1="10" x2="18" y2="10" stroke="#85cae6" stroke-width="1.2"/>
        </svg>
        <span>www.jollyhounds7.example</span>
      </li>
    </ul>

    <div class="card-footer-rule"></div>
  </article>
</body>
</html>
```